TorbCutters Website & website development in Wordpress

Simple website for a 5 pages with some 15 products for sale.
We will sell T shirts and other Viking mens grooming products.

*****Lady barbers****
Also the company that gets awarded this job needs to be able to give me a quote to build the site in wordpress, just a design will not work.

Target Market(s)

The adventurous person likes to travels and get a good haircut

Coding

Coded - Design and coding required

Number of Pages Required

5+ page

Font styles to use
Sans Serif

Colors
3176b5
33a6d7

Requirements
Must have
• Must have a product order page for T-Shirts
Must have a travel adventure page with up to 5 recommended adventures
Must have a link to our instagram @torbcuttersformen page that would allow a client to book a haircut
Should show female stylists cutting mens hair- So far the only pictures in the designs submitted are male barbers
Nice to have
• We have this set up in GoDaddy would like to use wordpress. Thanks!

```html
<!DOCTYPE html>
<html lang="en">
<head>
<meta charset="utf-8">
<title>TorbCutters</title>
<link href="https://fonts.googleapis.com/css2?family=Bebas+Neue&family=Karla:wght@400;500&display=swap" rel="stylesheet">
<style>
:root{
  --blue:#3176b5;
  --sky:#33a6d7;
  --navy:#1f4f8f;
  --button:#2b62ab;
  --ink:#3a3a3a;
  --muted:#5a5a5a;
  --light-band:#f0f1f3;
  --quote-band:#f4f4f4;
  --footer:#262626;
  --white:#ffffff;
  --star:#e0a21c;
}
*{box-sizing:border-box;margin:0;padding:0}
html,body{width:1200px;height:3782px;overflow:hidden}
body{position:relative;background:var(--white);font-family:"Karla",Arial,sans-serif;color:var(--ink)}
a{text-decoration:none}
.abs{position:absolute}
.display{font-family:"Bebas Neue",Impact,sans-serif;letter-spacing:.5px}

/* header */
.site-header{left:0;top:0;width:1200px;height:123px;background:var(--white)}
.brand-box{left:112px;top:0;width:147px;height:179px;background:var(--white);z-index:3;display:flex;align-items:center;justify-content:center;box-shadow:0 2px 6px rgba(0,0,0,.12)}
.brand-name{font-family:"Bebas Neue",Impact,sans-serif;font-size:30px;color:var(--navy)}
.main-nav a{position:absolute;top:50px;font-family:"Bebas Neue",Impact,sans-serif;font-size:17px;color:#2b2b2b;letter-spacing:.5px}
.main-nav a.current{color:var(--blue)}
.cart{left:1036px;top:34px;width:52px;height:52px;border:2px solid var(--navy);border-radius:50%}

/* hero */
.hero{left:0;top:123px;width:1200px;height:707px;background:linear-gradient(90deg,#221c19 0%,#3a2e28 45%,#6a5446 70%,#2a221e 100%)}
.hero-title{left:112px;top:355px;font-size:74px;color:var(--white);line-height:1}
.hero-sub{left:116px;top:452px;font-size:21px;line-height:35px;color:var(--white)}
.btn{display:flex;align-items:center;justify-content:center;background:var(--button);color:var(--white);font-family:"Bebas Neue",Impact,sans-serif;font-size:19px;letter-spacing:.5px;border-radius:3px}
.hero-btn{left:119px;top:542px;width:125px;height:50px}

/* welcome */
.welcome-photo{left:112px;top:917px;width:434px;height:382px;background:linear-gradient(160deg,#3d5e78,#6f8ea6 45%,#6b5a4c 80%,#4a3d33)}
.welcome-badge{left:388px;top:1143px;width:263px;height:238px;background:linear-gradient(180deg,var(--sky),#2a76c0)}
.section-title{font-size:40px;line-height:1;color:var(--navy)}
.section-title span{color:var(--sky)}
.rule{height:2px;width:44px;background:var(--blue)}
.body-copy{font-size:12.6px;line-height:25.7px;color:var(--muted);text-align:justify}

/* products */
.products{left:0;top:1447px;width:1200px;height:565px;background:var(--light-band)}
.product-card{top:1595px;width:231px;height:344px;background:var(--white);box-shadow:0 1px 4px rgba(0,0,0,.08);text-align:center}
.product-card .shot{position:absolute;left:20px;top:21px;width:191px;height:191px;border-radius:2px}
.product-card .stars{position:absolute;left:0;width:100%;top:225px;font-size:15px;color:var(--star);letter-spacing:1px}
.product-card .name{position:absolute;left:0;width:100%;top:253px;font-family:"Bebas Neue",Impact,sans-serif;font-size:27px;color:#444}
.product-card .price{position:absolute;left:0;width:100%;top:288px;font-family:"Bebas Neue",Impact,sans-serif;font-size:27px;color:var(--blue)}

/* promo */
.promo{left:0;top:2012px;width:1200px;height:521px;background:linear-gradient(100deg,#1f56a0 0%,#2660ad 45%,#2f86cc 70%,#2a9ad8 85%,#2a70c4 100%)}
.promo-lines{left:112px;top:2146px;font-size:32px;line-height:44px;color:var(--white)}
.promo-off{left:111px;top:2252px;font-size:66px;line-height:1;color:var(--white)}
.promo-btn{left:113px;top:2349px;width:163px;height:54px;border:2px solid var(--white);border-radius:27px;color:var(--white);display:flex;align-items:center;justify-content:center;font-size:20px}

/* travel */
.travel-photo{left:112px;top:2600px;width:495px;height:362px;background:linear-gradient(180deg,#f3d9a4 0%,#e7b477 40%,#8a7156 70%,#4b4236 100%)}

/* testimonial */
.testimonial{left:0;top:3078px;width:1200px;height:345px;background:var(--quote-band)}
.quote-text{left:209px;top:3172px;width:549px;font-family:Arial,Helvetica,sans-serif;font-size:13px;line-height:23px;color:#444;text-align:justify}
.quote-mark{font-family:Georgia,serif;font-size:34px;color:#b9b9b9;line-height:1}
.quote-name{left:211px;top:3286px;font-size:18px;color:var(--blue)}
.quote-date{left:211px;top:3310px;font-family:Arial,Helvetica,sans-serif;font-size:11.5px;color:#666}
.portrait{left:808px;top:3139px;width:196px;height:196px;border-radius:50%;border:4px solid #d9d9d9;background:radial-gradient(circle at 50% 45%,#c49a7e,#6b4a36 70%,#3b2a20)}

/* footer */
.site-footer{left:0;top:3423px;width:1200px;height:359px;background:var(--footer)}
.footer-brand{left:159px;top:3600px;width:206px;text-align:center;font-family:"Bebas Neue",Impact,sans-serif;font-size:40px;color:var(--white)}
.footer-head{font-size:21px;color:var(--white);font-weight:400}
.footer-list{font-family:Arial,Helvetica,sans-serif;font-size:12.5px;color:var(--white);list-style:none}
.footer-links li{height:30px;display:flex;align-items:center}
.footer-links li::before{content:"»";width:27px;font-size:14px}
.contact-list li{height:29.5px;display:flex;align-items:center}
.newsletter-copy{left:862px;top:3504px;width:230px;font-family:Arial,Helvetica,sans-serif;font-size:12px;line-height:22px;color:var(--white)}
.email-field{left:862px;top:3567px;width:226px;height:40px;background:var(--white);border-radius:2px;font-family:Arial,Helvetica,sans-serif;font-size:11px;color:#333;padding:13px 14px}
.submit-btn{left:862px;top:3618px;width:99px;height:35px;font-size:15px;border-radius:2px}
.copyright{left:0;top:3735px;width:1200px;text-align:center;font-family:Arial,Helvetica,sans-serif;font-size:14px;color:var(--white)}
</style>
</head>
<body>

<header>
  <div class="abs site-header"></div>
  <div class="abs brand-box"><span class="brand-name">TorbCutters</span></div>
  <nav class="main-nav">
    <a class="current" style="left:574px" href="#">Home</a>
    <a style="left:652px" href="#">About Us</a>
    <a style="left:752px" href="#">Products</a>
    <a style="left:856px" href="#">Gallery</a>
    <a style="left:950px" href="#">Contact Us</a>
  </nav>
  <div class="abs cart">
    <svg width="48" height="48" viewBox="0 0 48 48">
      <text x="24" y="19" font-family="Arial" font-size="12" fill="#1f4f8f" text-anchor="middle">0</text>
      <path d="M15 23h3l3 9h10l3-7H19" fill="none" stroke="#1f4f8f" stroke-width="2.2" stroke-linejoin="round"/>
      <circle cx="22" cy="35" r="1.8" fill="#1f4f8f"/><circle cx="30" cy="35" r="1.8" fill="#1f4f8f"/>
    </svg>
  </div>
</header>

<section>
  <div class="abs hero" role="img" aria-label="Barber styling a young man's hair in a dimly lit shop"></div>
  <h1 class="abs display hero-title">TORBCUTTERS</h1>
  <p class="abs display hero-sub">SED UT PERSPICIATIS UNDE OMNIS ISTE NATUS ERROR SIT<br>VOLUPTATEM ACCUSANTIUM DOLOREMQUE</p>
  <a class="abs btn hero-btn" href="#">Read More</a>
</section>

<section>
  <div class="abs welcome-photo" role="img" aria-label="Interior of the barbershop with chairs and framed landscape prints"></div>
  <div class="abs welcome-badge"></div>
  <h2 class="abs display section-title" style="left:708px;top:938px">WELCOME TO <span>TORBCUTTERS</span></h2>
  <div class="abs rule" style="left:711px;top:994px"></div>
  <p class="abs body-copy" style="left:711px;top:1018px;width:367px">Sed ut perspiciatis unde omnis iste natus error sit volu ptatem accusantium doloremque laudantium, totam rem aperiam, eaque ipsa quae ab illo inventore veritatis et quasi architecto beatae vitae dicta sunt explicabo ne emo enim ipsam voluptatem quia voluptas sit aspern atur aut odit aut fugit, sed quia consequuntur magni dolores eos qui ratione voluptatem sequi nesci unt neq ue porro quisquam est, qui dolorem ipsum quia dolor sit amet, consectetur, adipisci velit, sed</p>
  <a class="abs btn" style="left:712px;top:1273px;width:128px;height:46px" href="#">Read More</a>
</section>

<section>
  <div class="abs products"></div>
  <h2 class="abs display section-title" style="left:0;width:1200px;text-align:center;top:1494px">OUR <span>PRODUCTS</span></h2>
  <div class="abs rule" style="left:578px;top:1548px"></div>

  <div class="abs product-card" style="left:112px">
    <div class="shot" role="img" aria-label="Black grooming cream tube" style="background:linear-gradient(180deg,#fff 0%,#f1f1f1 100%)"></div>
    <div class="stars">☆☆☆☆☆</div><div class="name">Product Name</div><div class="price">$25.99</div>
  </div>
  <div class="abs product-card" style="left:361px">
    <div class="shot" role="img" aria-label="Razor with spare blade" style="background:linear-gradient(180deg,#fff 0%,#eef1f4 100%)"></div>
    <div class="stars">☆☆☆☆☆</div><div class="name">Product Name</div><div class="price">$25.99</div>
  </div>
  <div class="abs product-card" style="left:610px">
    <div class="shot" role="img" aria-label="Hair clipper set with combs and scissors" style="background:linear-gradient(180deg,#fff 0%,#ececec 100%)"></div>
    <div class="stars">☆☆☆☆☆</div><div class="name">Product Name</div><div class="price">$25.99</div>
  </div>
  <div class="abs product-card" style="left:859px">
    <div class="shot" role="img" aria-label="Beard oil, brush and balm tin" style="background:linear-gradient(180deg,#fafafa 0%,#f0e6dc 100%)"></div>
    <div class="stars">☆☆☆☆☆</div><div class="name">Product Name</div><div class="price">$25.99</div>
  </div>
</section>

<section>
  <div class="abs promo" role="img" aria-label="Folded blue t-shirts"></div>
  <p class="abs display promo-lines">SED UT PERSPICIATIS UNDE OMNIS<br>NATUS ERROR SIT VOLUPTATEM ACCUSANTIUM</p>
  <p class="abs display promo-off">50% OFF</p>
  <a class="abs display promo-btn" href="#">Shop Now</a>
</section>

<section>
  <div class="abs travel-photo" role="img" aria-label="Two hikers resting on a cliff above a misty valley at sunrise"></div>
  <h2 class="abs display section-title" style="left:661px;top:2653px">TRAVEL <span>ADVENTURE</span></h2>
  <div class="abs rule" style="left:665px;top:2706px"></div>
  <p class="abs body-copy" style="left:665px;top:2730px;width:391px">Sed ut perspiciatis unde omnis iste natus error sit volu pta tem accusantium doloremque laudantium, totam rem aperiam, eaque ipsa quae ab illo inventore veritatis et quasi architecto beatae vitae dicta sunt explicabo ne emo enim ipsam voluptatem omnis iste natus error</p>
  <a class="abs btn" style="left:667px;top:2881px;width:120px;height:47px" href="#">Get Started</a>
</section>

<section>
  <div class="abs testimonial"></div>
  <span class="abs quote-mark" style="left:190px;top:3150px">“</span>
  <p class="abs quote-text">Sed ut perspiciatis unde omnis iste natus error sit voluptatem accusantium doloremque laudantium, totam rem aperiam, eaque ipsa quae ab illo inventore veritatis et quasi architecto beatae vitae dicta sunt explicabo. Nemo enim ipsam voluptatem quia voluptas sit consequuntur magni dolores eos qui ratione voluptatem sequi nesciunt.</p>
  <span class="abs quote-mark" style="left:646px;top:3258px">”</span>
  <p class="abs display quote-name">ELSA BRANDT</p>
  <p class="abs quote-date">Posted On 07 July 2021</p>
  <div class="abs portrait" role="img" aria-label="Portrait of a smiling customer"></div>
</section>

<footer>
  <div class="abs site-footer"></div>
  <div class="abs footer-brand">TorbCutters</div>

  <h3 class="abs display footer-head" style="left:423px;top:3452px">Links</h3>
  <ul class="abs footer-list footer-links" style="left:427px;top:3496px">
    <li>Home</li><li>About Us</li><li>Products</li><li>Gallery</li><li>Contact us</li>
  </ul>

  <h3 class="abs display footer-head" style="left:617px;top:3452px">Contact</h3>
  <ul class="abs footer-list contact-list" style="left:620px;top:3499px">
    <li>Tele : 000-555-0148</li><li>Fax : 000-555-0149</li><li>hello@torbcutters.example</li><li>52 North Fjord Lane</li><li>Harbor Town 40218</li>
  </ul>

  <h3 class="abs display footer-head" style="left:862px;top:3452px">Newsletter</h3>
  <p class="abs newsletter-copy">Sed ut perspiciatis unde error sit vol uptatem accusantium...</p>
  <div class="abs email-field">Enter Email Id :</div>
  <a class="abs btn submit-btn" href="#">Submit</a>

  <p class="abs copyright">© Copyright 2021 TorbCutters.All Rights Reserved</p>
</footer>

</body>
</html>
```